Business cards to launch an education platform

Hi,
I am looking at having new business cards designed.
I am a startup, developing a web platform for schools and university, the education world. It's an online assessment system.
I would like a card that looks classy, and that is using the colors and the font of my logo.

I have attached:
1) my logo
2) A business card that I have designed quickly so you can have all the information required in the card, but I really don't like it.
3) The font that I am using (Lato Regular) to design my web platform
4) Some screenshots of my web platform so you can have a look at the style that I have.

Target Market(s)

Major market: Education system: Schools and university
Minor markets: Business in general

Industry/Entity Type

Business

Contact Information for Business Card

Clara Fenwick
Director

M: 0437 518 902
E: clara.fenwick@amberLoomSystems.com.au

Requirements
Must have
• The colors of my logo

```html
<!DOCTYPE html>
<html lang="en">
<head>
<meta charset="utf-8">
<title>Amber Loom Systems — Business Cards</title>
<link rel="stylesheet" href="https://fonts.googleapis.com/css2?family=Lato:wght@400;700&display=swap">
<style>
  :root {
    --backdrop: #e4e5e7;
    --card: #ffffff;
    --brand-deep: #1f5fa8;
    --brand-mid: #2d8fd8;
    --brand-light: #3ec3f0;
    --ink: #3a3f46;
    --ink-soft: #7a8088;
  }
  * { box-sizing: border-box; margin: 0; padding: 0; }
  html, body { width: 1200px; height: 755px; overflow: hidden; }
  body {
    background: var(--backdrop);
    font-family: "Lato", Arial, sans-serif;
    position: relative;
  }
  .card {
    position: absolute;
    width: 520px;
    height: 297px;
    background: var(--card);
    box-shadow: 0 6px 18px rgba(0,0,0,0.12);
    overflow: hidden;
  }
  .card--front { left: 50px; top: 229px; }
  .card--back  { left: 630px; top: 229px; }

  .brand {
    position: absolute;
    display: flex;
    align-items: center;
    gap: 14px;
  }
  .brand__mark {
    width: 58px; height: 58px;
    background: linear-gradient(135deg, var(--brand-mid), var(--brand-deep));
    flex: none;
  }
  .brand__name {
    color: var(--brand-mid);
    font-weight: 400;
    font-size: 30px;
    line-height: 1.05;
    letter-spacing: 1px;
    white-space: nowrap;
  }
  .card--front .brand { left: 50%; top: 50%; transform: translate(-50%, -50%); }

  .card--back .brand { right: 44px; top: 62px; gap: 10px; }
  .card--back .brand__mark { width: 40px; height: 40px; }
  .card--back .brand__name { font-size: 20px; }

  .edge-bar { position: absolute; }
  .edge-bar--left {
    left: 0; top: 120px; width: 12px; height: 177px;
    background: linear-gradient(180deg, var(--brand-mid), var(--brand-deep));
  }
  .edge-bar--right {
    right: 0; top: 0; width: 12px; height: 120px;
    background: linear-gradient(180deg, var(--brand-light), var(--brand-mid));
  }

  .person { position: absolute; left: 36px; top: 120px; }
  .person__name {
    color: var(--brand-mid);
    font-weight: 700;
    font-size: 17px;
    letter-spacing: 1px;
    text-transform: uppercase;
  }
  .person__role {
    color: var(--ink-soft);
    font-size: 8.5px;
    letter-spacing: 1.2px;
    text-transform: uppercase;
    margin-top: 2px;
  }

  .contacts {
    position: absolute;
    left: 50px; top: 168px;
    list-style: none;
    color: var(--ink);
    font-size: 11px;
    letter-spacing: 0.4px;
  }
  .contacts li { display: flex; align-items: flex-start; gap: 9px; margin-bottom: 8px; line-height: 1.3; }
  .contacts svg { width: 12px; height: 12px; flex: none; margin-top: 1px; fill: var(--brand-deep); }
  .contacts .phone { font-size: 13px; }
  .contacts .phone svg { margin-top: 2px; }
</style>
</head>
<body>

<section class="card card--front" aria-label="Card front">
  <div class="brand">
    <span class="brand__mark"></span>
    <span class="brand__name">Amber Loom<br>Systems</span>
  </div>
</section>

<section class="card card--back" aria-label="Card back">
  <span class="edge-bar edge-bar--right"></span>
  <span class="edge-bar edge-bar--left"></span>

  <div class="brand">
    <span class="brand__mark"></span>
    <span class="brand__name">Amber Loom<br>Systems</span>
  </div>

  <div class="person">
    <p class="person__name">Clara Fenwick</p>
    <p class="person__role">Director</p>
  </div>

  <ul class="contacts">
    <li class="phone">
      <svg viewBox="0 0 24 24"><path d="M7 1h10a2 2 0 0 1 2 2v18a2 2 0 0 1-2 2H7a2 2 0 0 1-2-2V3a2 2 0 0 1 2-2zm0 3v15h10V4zm5 16.2a1 1 0 1 0 0 .01z"/></svg>
      0437 518 902
    </li>
    <li>
      <svg viewBox="0 0 24 24"><path d="M2 5h20v14H2zm2 2v.5l8 5 8-5V7zm0 2.8V17h16V9.8l-8 5z"/></svg>
      clara.fenwick@amberLoomSystems.com.au
    </li>
    <li>
      <svg viewBox="0 0 24 24"><path d="M12 2a10 10 0 1 0 0 20 10 10 0 0 0 0-20zm6.9 6h-3a15 15 0 0 0-1.3-3.6A8 8 0 0 1 18.9 8zM12 4c.8 1.2 1.5 2.5 1.9 4h-3.8c.4-1.5 1.1-2.8 1.9-4zM4.3 14a8 8 0 0 1 0-4h3.4a16 16 0 0 0 0 4zm.8 2h3a15 15 0 0 0 1.3 3.6A8 8 0 0 1 5.1 16zm3-8h-3a8 8 0 0 1 4.3-3.6A15 15 0 0 0 8.1 8zM12 20c-.8-1.2-1.5-2.5-1.9-4h3.8c-.4 1.5-1.1 2.8-1.9 4zm2.3-6H9.7a14 14 0 0 1 0-4h4.6a14 14 0 0 1 0 4zm.3 5.6a15 15 0 0 0 1.3-3.6h3a8 8 0 0 1-4.3 3.6zm1.7-5.6a16 16 0 0 0 0-4h3.4a8 8 0 0 1 0 4z"/></svg>
      www.amberloomsystems.com.au
    </li>
    <li>
      <svg viewBox="0 0 24 24"><path d="M12 3 2 11h3v10h5v-6h4v6h5V11h3z"/></svg>
      <span>12 Harbour Road<br>Level 3, North Wing</span>
    </li>
  </ul>
</section>

</body>
</html>
```